I need a business card for my original fine art pieces

I would like a business card design including a logo design for a new business in the art world. I am based in the Hunter Valley NSW Australia. I am a contemporary figurative, encaustic and wildlife artist. I would like to be able to upload my email and mobile number to this as well. This design should be one that I can incorporate into banners and flyers etc. Id like to incorporate one of my own images or partial image into the background or somewhere below. My initials are RJ and I would like these used as a logo type. I would like the use of some colour and it to be bright and catchy. The final design should communicate artwork custom made and commissions available.

Overview: Original Fine Artworks for sale, online, art galleries etc, Custom made to order and by commission.

Target market is world wide audience and corporate world

My figurative work is painted using acrylics in a lot of natural ochre colours that reflect the Australian Outback, on canvas, linen, paper or board: My encaustic work is created in a contemporary abstract style using a blow torch and a made with a medium of 100% pure bees wax, Damar resin, mixed media and coloured pigments, applied to Birch board. My wildlife are created using coloured pencil and mixed media on a variety of paper types or board.

```html
<!DOCTYPE html>
<html lang="en">
<head>
<meta charset="utf-8">
<title>Ruby Jarrah – Business Card</title>
<link rel="stylesheet" href="https://fonts.googleapis.com/css2?family=Cinzel:wght@400;500&family=Source+Sans+3:wght@400&display=swap">
<style>
  :root {
    --backdrop: #646464;
    --card-dark: #111215;
    --accent: #ff4a00;
    --accent-deep: #e84300;
    --white: #ffffff;
  }
  html, body {
    margin: 0;
    padding: 0;
    width: 1200px;
    height: 900px;
    overflow: hidden;
    background: var(--backdrop);
  }
  .stage {
    position: relative;
    width: 1200px;
    height: 900px;
    background: var(--backdrop);
  }
  .card {
    position: absolute;
    top: 200px;
    width: 310px;
    height: 501px;
    overflow: hidden;
  }
  .card--front {
    left: 265px;
    background: var(--card-dark);
    border-radius: 66px 0 66px 0;
  }
  .card--back {
    left: 641px;
    width: 309px;
    background: var(--accent);
    border-radius: 0 66px 0 66px;
  }
  .brand-ring {
    position: absolute;
    left: 119px;
    top: 54px;
    width: 86px;
    height: 86px;
    border: 3px solid var(--accent);
    border-radius: 50%;
  }
  .brand {
    position: absolute;
    left: 0;
    width: 100%;
    text-align: center;
    margin: 0;
  }
  .brand__name {
    display: block;
    font-family: "Cinzel", "Times New Roman", serif;
    font-weight: 500;
    font-size: 30px;
    line-height: 1;
    letter-spacing: 0.5px;
  }
  .brand__tagline {
    display: block;
    font-family: "Source Sans 3", Arial, sans-serif;
    font-size: 13px;
    letter-spacing: 2.2px;
    color: var(--white);
    margin-top: 5px;
  }
  .card--front .brand { top: 148px; left: 10px; }
  .card--front .brand__name { color: var(--accent); }
  .card--back .brand { top: 387px; }
  .card--back .brand__name { color: var(--white); font-size: 32px; }
  .card--back .brand__tagline { font-size: 14px; margin-top: 4px; }
  .person {
    position: absolute;
    left: 31px;
    top: 333px;
    font-family: "Source Sans 3", Arial, sans-serif;
  }
  .person__name {
    margin: 0;
    color: var(--accent);
    font-size: 21px;
    font-weight: 400;
    line-height: 1.1;
  }
  .person__role {
    margin: 3px 0 0;
    color: var(--white);
    font-size: 14px;
  }
  .contact {
    position: absolute;
    left: 31px;
    top: 411px;
    margin: 0;
    padding: 0;
    list-style: none;
    font-family: "Source Sans 3", Arial, sans-serif;
    font-size: 14px;
    color: var(--white);
  }
  .contact__item {
    display: flex;
    align-items: center;
    gap: 8px;
    height: 18px;
  }
  .contact__icon {
    width: 11px;
    height: 11px;
    fill: var(--accent);
    flex: none;
  }
  .back-rings {
    position: absolute;
    inset: 0;
  }
</style>
</head>
<body>
<main class="stage">
  <section class="card card--front" aria-label="Card front">
    <div class="brand-ring" aria-hidden="true"></div>
    <h1 class="brand">
      <span class="brand__name">Ruby Jarrah</span>
      <span class="brand__tagline">ORIGINAL FINE ARTWORKS</span>
    </h1>
    <div class="person">
      <p class="person__name">Daniel Hart</p>
      <p class="person__role">Managing Director</p>
    </div>
    <ul class="contact">
      <li class="contact__item">
        <svg class="contact__icon" viewBox="0 0 24 24" aria-hidden="true"><path d="M6.6 10.8a15.2 15.2 0 0 0 6.6 6.6l2.2-2.2c.3-.3.7-.4 1-.2 1.1.4 2.3.6 3.6.6.6 0 1 .4 1 1V20c0 .6-.4 1-1 1A17 17 0 0 1 3 4c0-.6.4-1 1-1h3.5c.6 0 1 .4 1 1 0 1.3.2 2.5.6 3.6.1.3 0 .7-.2 1z"/></svg>
        <span>044-987 654 321</span>
      </li>
      <li class="contact__item">
        <svg class="contact__icon" viewBox="0 0 24 24" aria-hidden="true"><path d="M2 5h20v14H2z" fill="none"/><path d="M2 5h20v2l-10 6L2 7zM2 9l10 6 10-6v10H2z"/></svg>
        <span>hello@rjarrah.com</span>
      </li>
      <li class="contact__item">
        <svg class="contact__icon" viewBox="0 0 24 24" aria-hidden="true"><path d="M10 14a5 5 0 0 0 7 0l4-4a5 5 0 0 0-7-7l-1.5 1.5 1.4 1.4L15.4 4.4a3 3 0 0 1 4.2 4.2l-4 4a3 3 0 0 1-4.2 0zM14 10a5 5 0 0 0-7 0l-4 4a5 5 0 0 0 7 7l1.5-1.5-1.4-1.4-1.5 1.5a3 3 0 0 1-4.2-4.2l4-4a3 3 0 0 1 4.2 0z"/></svg>
        <span>www.rubyjarrah.com</span>
      </li>
    </ul>
  </section>

  <section class="card card--back" aria-label="Card back">
    <svg class="back-rings" viewBox="0 0 309 501" aria-hidden="true">
      <circle cx="6" cy="220" r="166" fill="none" stroke="var(--accent-deep)" stroke-width="9" opacity="0.7"/>
      <circle cx="320" cy="300" r="166" fill="none" stroke="var(--accent-deep)" stroke-width="9" opacity="0.7"/>
    </svg>
    <p class="brand">
      <span class="brand__name">Ruby Jarrah</span>
      <span class="brand__tagline">ORIGINAL FINE ARTWORKS</span>
    </p>
  </section>
</main>
</body>
</html>
```